Holiday Rental Company Flyer Design (DL not A5)

Note from Brandloom Administration: The category sizing selected is A5, however the project requires DL sized artwork. Please refer to the DL template link below while the 'Special Requirements' are updated accordingly.

Project Brief:
We need a double sided DL flyer designed for an up market Holiday Rental Company that portrays a personalised approach to property management. These are to be used for letter box drops to homes we're specifically targeting so the design should be modern, complimentary colour palette, uncluttered & visually appealing.

Please Download the DL Template from Quillora here: http://www.quillora.com.au/ql/ns/propath/UploadResources.aspx?selectedTab=0?pfid=KMT&pf_id=KMT&xnav=easypath-upload-image#Templates

Target Market(s)

Wealthy Home Owners

Industry/Entity Type

It Company

Other font styles liked:
• Avant Garde Extra Light & Demi

Colors
33b8a4

Requirements
Must have
• DL Flyer sizes (210mm width x 99mm width, plus 3mm bleed)
• Front: Logo, Main Image & Grab
• Back: Contact Details & Brief Description of our business
• Images: Ideally the main image should be the house with the pool but alternatively a lifestyle images could also be used.
Nice to have
• A creative designer!
Should not have
• Clutter & busy designs

```html
<!DOCTYPE html>
<html lang="en">
<head>
<meta charset="utf-8">
<title>Harbourline Stays – DL Flyer Front</title>
<link rel="stylesheet" href="https://fonts.googleapis.com/css2?family=Poppins:wght@200;700&display=swap">
<style>
  :root {
    --page-bg: #ffffff;
    --page-edge: #3a3a3a;
    --brand-teal: #10b28f;
    --brand-teal-light: #72d6c6;
    --headline: #333333;
    --quote-mark: #e9f4f2;
    --logo-text: #ffffff;
    --sky: #cfe3ee;
    --sea: #4fb7c2;
    --foliage: #3f6b2c;
    --terrace: #e8e1d6;
  }

  * { margin: 0; padding: 0; box-sizing: border-box; }

  html, body {
    width: 1200px;
    height: 849px;
    overflow: hidden;
    background: var(--page-bg);
  }

  .canvas {
    position: relative;
    width: 1200px;
    height: 849px;
    border: 1px solid var(--page-edge);
    background: var(--page-bg);
  }

  .flyer {
    position: absolute;
    left: 176px;
    top: 224px;
    width: 848px;
    height: 400px;
    background: var(--brand-teal);
    overflow: hidden;
  }

  .hero-photo {
    position: absolute;
    left: 0;
    top: 0;
    width: 790px;
    height: 366px;
    border-right: 4px solid var(--brand-teal-light);
    border-bottom: 4px solid var(--brand-teal-light);
    border-bottom-right-radius: 56px;
    background: linear-gradient(
      to bottom,
      var(--sky) 0%,
      #d9ebf2 14%,
      var(--sea) 22%,
      #3fa9b3 38%,
      var(--foliage) 44%,
      #2f5a24 64%,
      #9fc9c9 68%,
      var(--terrace) 72%,
      #ddd5c8 100%
    );
  }

  .headline {
    position: absolute;
    left: 110px;
    top: 24px;
    width: 380px;
    font-family: "Poppins", sans-serif;
    font-weight: 700;
    font-size: 30px;
    line-height: 35px;
    letter-spacing: -0.2px;
    color: var(--headline);
    text-align: center;
  }

  .headline .quote {
    color: var(--quote-mark);
    font-size: 24px;
    vertical-align: top;
  }

  .brand-badge {
    position: absolute;
    left: 652px;
    top: 32px;
    width: 140px;
    height: 144px;
    background: var(--brand-teal);
    border: 4px solid var(--brand-teal-light);
    border-right: none;
    display: flex;
    flex-direction: column;
    align-items: center;
    justify-content: center;
    gap: 12px;
  }

  .brand-name {
    font-family: "Poppins", sans-serif;
    font-weight: 200;
    font-size: 19px;
    line-height: 26px;
    letter-spacing: 2px;
    color: var(--logo-text);
    text-align: center;
    text-transform: uppercase;
  }

  .brand-dot {
    width: 22px;
    height: 22px;
    border: 1px solid var(--logo-text);
    border-radius: 50%;
  }
</style>
</head>
<body>
  <div class="canvas">
    <section class="flyer">
      <div class="hero-photo" role="img" aria-label="Photo of two brown sun loungers on a pale terrace beside an infinity pool, with tropical trees and a turquoise sea beyond, framed by open glass doors"></div>

      <h1 class="headline">
        <span class="quote">&ldquo;</span>Holiday Rental Management with a difference<span class="quote">&rdquo;</span>
      </h1>

      <div class="brand-badge">
        <p class="brand-name">Harbourline<br>Stays</p>
        <span class="brand-dot"></span>
      </div>
    </section>
  </div>
</body>
</html>
```